Exclusive beauty salon needs a price list or services booklet

I need a new very attractive flyer for my beauty salon, containing information on the different services and their prices.
In attachment you can find a pdf of the "old" one, but I'd love to have a beautifully designed new one!
I'd love to have a booklet in format 148 x 148 mm, or in US format, containing 12 or 16 pages, but if you can offer other nice looking designs they are welcome!
The services that need to come in the booklet with their prices can all be found on my website: www.atelierverano.be, starting with
Gelaatsverzorging
Wimperverlenging
Suikerontharing
Wimperlifting
Permanente Make Up
Airbrush Tanning

Target Market(s)

woman from 20 to 89 years old

Industry/Entity Type

Beauty Salon

Font styles to use
Sans Serif

Colors

Designer to choose colors to be used in the design.

Requirements
Must have
• a classy nice look, it must contain details about the services from my beauty salon and their prices, and nice pictures.
• The Names, prices and explanations of the services can easily be found on my website: www.atelierverano.be
Nice to have
• In attachment you can find the "old" price list in pdf, what I need now is a "new booklet" with the new logo and updated services price list.
• I need a very nice and attractive looking booklet, classy chique, Paris chique, looking very expensive.
Should not have
• Not too much colors, not too curly, but still feminine

```html
<!DOCTYPE html>
<html lang="nl">
<head>
<meta charset="utf-8">
<title>Atelier Verano – Permanente Make Up</title>
<link href="https://fonts.googleapis.com/css2?family=Didact+Gothic&display=swap" rel="stylesheet">
<style>
  :root{
    --backdrop:#9d9d9d;
    --paper:#f7f7f7;
    --paper-shade:#ececec;
    --rose:#dfa4ae;
    --rose-light:#f1d6da;
    --teal:#76c6c0;
    --teal-light:#cdebe8;
    --ink:#6d6d6d;
    --note-bg:#e4eeee;
    --photo-rose:#c9a3a8;
    --photo-rose-light:#e6d0d3;
    --photo-grey:#dcdcdc;
    --photo-grey-light:#f0f0f0;
  }
  *{box-sizing:border-box;margin:0;padding:0}
  ul{list-style:none}
  html,body{width:1200px;height:523px;overflow:hidden}
  body{background:var(--backdrop);font-family:"Didact Gothic",sans-serif;color:var(--ink);position:relative}
  .spread{position:absolute;left:140px;top:26px;width:920px;height:470px;display:flex}
  .page{position:relative;width:460px;height:470px;background:linear-gradient(180deg,var(--paper),var(--paper-shade));overflow:hidden}
  .page--left{box-shadow:inset -14px 0 18px -14px rgba(0,0,0,.18)}
  .page--right{box-shadow:inset 14px 0 18px -14px rgba(0,0,0,.18)}
  .service{position:absolute;left:0;right:0}
  .service-bar{position:absolute;height:19px;display:flex;align-items:center;justify-content:space-between;padding:0 12px 0 14px;color:#fff;font-size:12.5px;font-weight:400;letter-spacing:.4px;text-transform:uppercase;white-space:nowrap}
  .service-bar--rose{background:linear-gradient(90deg,var(--rose),var(--rose-light) 75%,var(--rose))}
  .service-bar--teal{background:linear-gradient(90deg,var(--teal),var(--teal-light) 75%,var(--teal))}
  .price{font-size:10px;letter-spacing:0}
  .body{position:absolute;font-size:8.6px;line-height:13.6px;color:var(--ink)}
  .bullets li{position:relative;padding-left:10px}
  .bullets li::before{content:"";position:absolute;left:2px;top:5.5px;width:3px;height:3px;border-radius:50%;background:var(--rose)}
  .bullets--teal li::before{background:var(--teal)}
  .bullets--spaced li{margin:6px 0 8px}
  .visual{position:absolute;width:74px;height:74px;border-radius:50%;border:3px solid #fff;box-shadow:0 2px 6px rgba(0,0,0,.25)}
  .visual--rose{background:linear-gradient(160deg,var(--photo-rose-light),var(--photo-rose))}
  .visual--grey{background:linear-gradient(160deg,var(--photo-grey-light),var(--photo-grey))}
  .note{position:absolute;left:31px;right:0;top:195px;height:209px;background:var(--note-bg)}
  .note-intro{position:absolute;left:26px;top:14px;width:320px;font-size:9px;line-height:12.6px;padding-left:11px;border-left:1px solid var(--teal)}
  .note-list{position:absolute;left:38px;top:66px;width:300px;font-size:9px;line-height:12.6px}
  .note-list li{margin-bottom:12px}
  .brand{position:absolute;right:22px;bottom:26px;text-align:center;color:#555}
  .brand-name{font-size:11px;letter-spacing:1px}
  .brand-tag{font-size:5px;letter-spacing:1.4px;text-transform:uppercase;margin-top:2px}
</style>
</head>
<body>
<main class="spread">
  <section class="page page--left">
    <article class="service" style="top:16px">
      <h2 class="service-bar service-bar--rose" style="left:26px;right:0"><span>Fijne eyeliner boven (wimperinvulling) het oog</span><span class="price">€185</span></h2>
      <div class="body" style="left:28px;top:25px;width:290px">
        <p>De fijne eyeliner of wimperinvulling om uw ogen op een subtiele manier iets meer accentueren en laten spreken!</p>
        <ul class="bullets bullets--spaced">
          <li>Een eye-liner met subtiele klasse!</li>
          <li>uw ogen zullen meer spreken en u hoeft zich geen zorgen meer te maken over uitgelopen lijntjes of panda ogen.</li>
          <li>een echte Liner zonder het too much effect.</li>
        </ul>
      </div>
      <div class="visual visual--rose" style="left:322px;top:37px" role="img" aria-label="Close-up photo of an eye with fine eyeliner"></div>
    </article>

    <article class="service" style="top:157px">
      <h2 class="service-bar service-bar--teal" style="left:26px;right:0"><span>Wenkbrauwen hairstroke techniek</span><span class="price">€320</span></h2>
      <div class="body" style="left:28px;top:22px;width:300px">
        <p>voor wie?</p>
        <ul class="bullets bullets--teal">
          <li>je wenst een hyper realistisch natuurlijk resultaat</li>
          <li>je hebt weinig tot geen eigen haartjes</li>
          <li>je bent het niet gewend om make up op je wenkbrauwen te gebruiken</li>
        </ul>
        <p>oplossing:</p>
        <ul class="bullets bullets--teal">
          <li>er worden hairstrokes (fijne haartjes) gepigmenteerd op de huid</li>
          <li>voor een vollere wenkbrauw</li>
          <li>met een heel natuurlijk look</li>
        </ul>
      </div>
      <div class="visual visual--grey" style="left:322px;top:45px" role="img" aria-label="Photo of a hairstroke eyebrow result"></div>
    </article>

    <article class="service" style="top:306px">
      <h2 class="service-bar service-bar--rose" style="left:26px;right:0"><span>Wenkbrauwen shading brow of poederwenkbrauw</span><span class="price">€320</span></h2>
      <div class="body" style="left:28px;top:22px;width:300px">
        <p>voor wie?</p>
        <ul class="bullets">
          <li>je wil elke dag mooi gevormde wenkbrauwen</li>
          <li>je houdt van de soft make up look</li>
          <li>je hebt weinig tot voldoende eigen haartjes</li>
        </ul>
        <p>oplossing:</p>
        <ul class="bullets">
          <li>intensere kleur geven aan de wenkbrauw</li>
          <li>mooie vorm geven aan de wenkbrauw</li>
          <li>voor een mooie, zachte make up look</li>
        </ul>
        <p>gezien bij Lena Dorval</p>
      </div>
      <div class="visual visual--grey" style="left:322px;top:49px" role="img" aria-label="Photo of a powder shaded eyebrow result"></div>
    </article>
  </section>

  <section class="page page--right">
    <article class="service" style="top:19px">
      <h2 class="service-bar service-bar--teal" style="left:27px;right:5px"><span>Wenkbrauwen power brow</span><span class="price">€320</span></h2>
      <div class="body" style="left:28px;top:22px;width:300px">
        <p>voor wie:</p>
        <ul class="bullets bullets--teal">
          <li>je wenst een meer uitgesproken resultaat</li>
          <li>je draagt dagelijks make up aan de wenkbrauwen</li>
          <li>je hebt voldoende haartjes</li>
        </ul>
        <p>oplossing:</p>
        <ul class="bullets bullets--teal">
          <li>shading techniek + hairstroke techniek = power brow</li>
          <li>voller maken van de eigen wenkbrauw</li>
          <li>meer kleur en vorm geven</li>
          <li>voor de echte make up look</li>
        </ul>
        <p>Gezien bij Mila Varenne</p>
      </div>
      <div class="visual visual--grey" style="left:349px;top:54px" role="img" aria-label="Photo of a power brow eyebrow result"></div>
    </article>

    <aside class="note">
      <p class="note-intro">Alles wordt uitvoerig besproken en uitgetekend zo ziet u al hoe uw permanente make up er zal uitzien en je kan zelf aangeven of je deze fijner of net iets dikker wenst. Ik geef graag advies voor uw mooiste resultaat.</p>
      <ul class="note-list bullets bullets--teal">
        <li>breng gerust foto's mee van resultaten die je mooi vindt;</li>
        <li>kies zelf de vorm van uw permanente make up, alles wordt eerst uitgetekend;</li>
        <li>alle pigmenten zijn conform de EU wetgeving;</li>
        <li>geen AZO, Nickel, Zware metalen, Pak's in de pigmenten;</li>
        <li>ook voor mensen die extreem allergisch zijn.</li>
      </ul>
    </aside>

    <footer class="brand">
      <p class="brand-name">Atelier Verano</p>
      <p class="brand-tag">beauty atelier</p>
    </footer>
  </section>
</main>
</body>
</html>
```